Tallon Electrical Business Card

We need a business card design for our family-run electrical contracting business based in Western Australia called 'Tallon Electrical'. We provide electrical services including residential, commercial and industrial. We aim for individual business cards to be made for all of our employees. We already have a company logo, which we require to be featured on the design. We would like simple, sleek and vibrant designs, which incorporate our logo and represent our business. We do not want anything involving too many graphics/images. We like the colours red, black, white and all shades of grey. The final design should communicate professionalism and trustworthiness.
We require the following contact information:
Name- Grant Pellow
EC 5871
Mobile number- 0455 870 219
Fax number (including area code)- (08) 9560 2831
Email adress- name@tallonelectrical.com.au
Electrical
- ITC Handel Bold

```html
<!DOCTYPE html>
<html lang="en">
<head>
<meta charset="utf-8">
<title>Tallon Electrical Business Card</title>
<link rel="stylesheet" href="https://fonts.googleapis.com/css2?family=Arimo:wght@400;700&display=swap">
<style>
  :root {
    --red: #d81a1f;
    --red-deep: #c4161b;
    --black: #1a1a1a;
    --grey-text: #4a4a4a;
    --card-white: #f4f4f3;
    --backdrop: #8d8d8d;
  }
  * { box-sizing: border-box; margin: 0; padding: 0; }
  html, body { width: 1200px; height: 720px; overflow: hidden; }
  body {
    background: var(--backdrop);
    font-family: "Arimo", Arial, sans-serif;
    display: flex;
    align-items: center;
    justify-content: center;
    gap: 40px;
  }
  .card {
    width: 540px;
    height: 330px;
    position: relative;
    box-shadow: 0 6px 18px rgba(0,0,0,0.25);
  }

  /* Back of card */
  .card-back {
    background: var(--red);
    display: flex;
    flex-direction: column;
    align-items: center;
    justify-content: center;
    gap: 22px;
  }
  .card-back .wordmark { color: #fff; font-size: 30px; }
  .card-back .website { color: #fff; font-size: 17px; letter-spacing: 0.2px; }
  .card-back .website b { font-weight: 700; }

  /* Front of card */
  .card-front { background: var(--card-white); }
  .wordmark {
    display: flex;
    align-items: center;
    gap: 12px;
    font-weight: 700;
    text-transform: uppercase;
    letter-spacing: 1px;
  }
  .wordmark .mark-square {
    width: 22px; height: 22px; background: currentColor; flex: none;
  }
  .card-front .wordmark {
    position: absolute;
    top: 48px; left: 0; right: 0;
    justify-content: center;
    color: var(--black);
    font-size: 28px;
  }
  .holder {
    position: absolute;
    top: 118px; left: 40px;
  }
  .holder-name { color: var(--red); font-weight: 700; font-size: 17px; }
  .holder-role { color: var(--grey-text); font-size: 14px; margin-top: 3px; }

  .divider {
    position: absolute;
    left: 262px; top: 160px;
    width: 1px; height: 120px;
    background: #d2d2d2;
  }
  .contact {
    position: absolute;
    left: 284px; top: 162px;
    list-style: none;
    color: var(--grey-text);
    font-size: 14.5px;
    line-height: 1.3;
  }
  .contact li {
    display: flex;
    align-items: flex-start;
    gap: 10px;
    margin-bottom: 5px;
  }
  .contact svg { width: 13px; height: 13px; flex: none; margin-top: 2px; fill: var(--red); }
</style>
</head>
<body>

  <section class="card card-back" aria-label="Card back">
    <div class="wordmark"><span class="mark-square"></span>Tallon Electrical</div>
    <p class="website">www.<b>tallonelectrical</b>.com.au</p>
  </section>

  <section class="card card-front" aria-label="Card front">
    <div class="wordmark"><span class="mark-square" style="color:var(--red)"></span>Tallon Electrical</div>

    <div class="holder">
      <p class="holder-name">Grant Pellow</p>
      <p class="holder-role">Director</p>
    </div>

    <span class="divider"></span>

    <ul class="contact">
      <li>
        <svg viewBox="0 0 12 12" aria-hidden="true"><path d="M6 0a4 4 0 0 0-4 4c0 3 4 8 4 8s4-5 4-8a4 4 0 0 0-4-4zm0 5.6A1.6 1.6 0 1 1 6 2.4a1.6 1.6 0 0 1 0 3.2z"/></svg>
        <span>EC 5871, address<br>town here 6542U</span>
      </li>
      <li>
        <svg viewBox="0 0 12 12" aria-hidden="true"><path d="M3 0h6a1 1 0 0 1 1 1v10a1 1 0 0 1-1 1H3a1 1 0 0 1-1-1V1a1 1 0 0 1 1-1zm.5 1.5v8h5v-8z"/></svg>
        <span>0455 870 219</span>
      </li>
      <li>
        <svg viewBox="0 0 12 12" aria-hidden="true"><path d="M3 0h6v3H3zM1 4h10a1 1 0 0 1 1 1v5H0V5a1 1 0 0 1 1-1zm2 5v3h6V9z"/></svg>
        <span>(08) 9560 2831</span>
      </li>
      <li>
        <svg viewBox="0 0 12 12" aria-hidden="true"><path d="M0 2h12v8H0zm1.2 1 4.8 3.6L10.8 3z"/></svg>
        <span>name@tallonelectrical.com.au</span>
      </li>
    </ul>
  </section>

</body>
</html>
```